Killer Webpage Design

I currently have a self-hosted webpage through wordpress at www.velmarqstudio.com - the content is complete and I'm happy with this but I need it designed (no coding) to complete my requirements. I'm happy to take designs which are non-Wordpress if there is specific advantage in this.

My full branding logos are attached along with color files. My main aim is consistent branding across all areas (social media, business cards, emails, websites). I have the rest running but am not happy with the available default selections from Wordpress.

I would prefer to use the darker blue version of the logo as I feel this has more standout in online media, however I would appreciate submissions with both variants to help me choose.

With the homepage I will also want to see blog pages and category pages designed but this can come after I have selected a design to go with,

Sites that I like and are related to my business include the following:
http://www.brindlepath.com/au/accounting-software/
http://www.tasklanternpro.com/home.aspx
https://pelicoin.com/register
Updates

Apologies for the confusion - to clarify for designers I am looking for design only, no coding.

FYI - i have now uploaded business cards for an idea of the contemporary style of design completed so far.

Target Market(s)

small to medium business. Not systemised but looking for help and support.

Industry/Entity Type

Business

Requirements
Must have
• I'm looking for a minimalist professional page, with the ability to easily add new sections when required. I will also need a CMS to add blog posts on the go, with the same features that it currently has (comments, social logon etc)

```html
<!DOCTYPE html>
<html lang="en">
<head>
<meta charset="utf-8">
<title>Velmarq Studio – Specialist Business Consultants</title>
<link href="https://fonts.googleapis.com/css2?family=PT+Sans:wght@400;700&display=swap" rel="stylesheet">
<style>
  :root {
    --navy: #062232;
    --navy-soft: #0b3346;
    --teal: #0bbcc4;
    --teal-head: #14a6b5;
    --orange: #f07b36;
    --text: #7d7d7d;
    --text-dark: #666;
    --page: #f6f6f6;
    --white: #ffffff;
    --line: #dcdcdc;
  }
  * { margin: 0; padding: 0; box-sizing: border-box; }
  html, body { width: 1131px; height: 1200px; overflow: hidden; }
  body {
    position: relative;
    font-family: "PT Sans", Arial, sans-serif;
    background: var(--page);
    color: var(--text);
  }
  .abs { position: absolute; }

  /* Header */
  .site-header { left: 0; top: 0; width: 1131px; height: 100px; background: var(--navy); }
  .brand { left: 178px; top: 30px; display: flex; align-items: center; gap: 10px; }
  .brand-dot { width: 36px; height: 36px; border-radius: 50%; background: var(--teal); }
  .brand-name { color: var(--white); font-size: 27px; font-weight: 700; letter-spacing: -0.3px; }
  .social { top: 32px; width: 36px; height: 36px; border-radius: 50%; background: var(--navy-soft); }

  /* Navigation */
  .main-nav { left: 0; top: 100px; width: 1131px; height: 37px; background: var(--white); }
  .main-nav ul { position: absolute; left: 187px; top: 0; height: 37px; display: flex; align-items: center; list-style: none; }
  .main-nav li { font-size: 11px; color: #666; letter-spacing: 0.2px; text-transform: uppercase; }
  .main-nav li.active { color: var(--teal-head); }
  .main-nav li + li::before { content: "|"; color: #999; margin: 0 14px; }

  /* Hero */
  .hero { left: 0; top: 137px; width: 1131px; height: 387px; background: var(--teal); }
  .hero-title { left: 177px; top: 100px; color: var(--white); line-height: 1; }
  .hero-title .small { display: block; font-size: 25px; font-weight: 400; }
  .hero-title .big { display: block; font-size: 34px; font-weight: 700; letter-spacing: 0.5px; margin-top: 1px; }
  .hero-quote { left: 198px; top: 166px; width: 210px; color: var(--white); font-size: 12.6px; line-height: 17.8px; }
  .qmark { color: var(--white); font-size: 26px; font-weight: 700; line-height: 1; }
  .qmark.open { left: 177px; top: 166px; }
  .qmark.close { left: 406px; top: 253px; }
  .hero-visual {
    left: 442px; top: 37px; width: 511px; height: 303px;
    background: linear-gradient(180deg, #1b1b1b 0%, #2a2a2a 6%, #7d8a99 20%, #c9b59b 70%, #2a2a2a 91%, #cfd2d4 93%, #9ea3a6 100%);
    border-radius: 10px 10px 4px 4px;
  }
  .slider-dots { left: 681px; top: 348px; display: flex; gap: 7px; }
  .slider-dots span { width: 12px; height: 12px; border-radius: 50%; background: var(--white); }
  .slider-dots span.current { background: transparent; border: 2px solid var(--white); }

  /* Section headings */
  .section-title { display: flex; align-items: center; gap: 8px; color: var(--teal-head); font-size: 17px; font-weight: 700; text-transform: uppercase; letter-spacing: 0.2px; }
  .section-title::before { content: ""; width: 14px; height: 14px; border-radius: 50%; background: var(--orange); margin-right: 8px; }

  /* Welcome */
  .welcome { left: 178px; top: 557px; width: 490px; }
  .welcome-body { margin-top: 18px; font-size: 10.6px; line-height: 16.2px; text-align: justify; }
  .welcome-photo { float: left; width: 196px; height: 135px; margin: 0 14px 1px 0; background: linear-gradient(135deg, #3b3f44 0%, #8c8f93 45%, #e6e2dc 100%); }

  /* Services */
  .services { left: 699px; top: 557px; width: 260px; }
  .services ul { list-style: none; margin-top: 14px; }
  .services li { position: relative; padding-left: 15px; font-size: 10.8px; line-height: 24.2px; color: var(--text-dark); }
  .services li::before { content: ""; position: absolute; left: 0; top: 10px; width: 5px; height: 5px; border-radius: 50%; background: var(--orange); }

  /* Footer band */
  .footer-band { left: 0; top: 1043px; width: 1131px; height: 92px; background: var(--teal); }
  .footer-nav { left: 181px; top: 1103px; display: flex; list-style: none; }
  .footer-nav li { color: var(--white); font-size: 12px; }
  .footer-nav li + li::before { content: "|"; margin: 0 14px; }

  /* Cards */
  .card { top: 875px; height: 210px; background: var(--white); border: 1px solid var(--line); border-radius: 3px; padding: 21px 19px; }
  .card.blog { left: 177px; width: 387px; }
  .card.comments { left: 566px; width: 395px; }
  .card-arrows { position: absolute; right: 19px; top: 25px; display: flex; gap: 2px; }
  .card-arrows span { width: 16px; height: 16px; background: var(--orange); display: flex; align-items: center; justify-content: center; }
  .card-link { display: block; margin-top: 24px; color: var(--teal-head); font-size: 11px; }
  .card-link + p { margin-top: 5px; }
  .card p { font-size: 10.6px; line-height: 16.2px; color: var(--text); }
  .card .sub-link { margin-top: 9px; }
  .byline { margin-top: 7px; color: var(--teal-head); font-size: 11px; line-height: 16.2px; }

  /* Bottom footer */
  .site-footer { left: 0; top: 1135px; width: 1131px; height: 65px; background: var(--navy); }
  .copyright { left: 176px; top: 25px; color: var(--white); font-size: 11.4px; }
  .footer-brand { left: 824px; top: 20px; display: flex; align-items: center; gap: 7px; }
  .footer-brand .brand-dot { width: 26px; height: 26px; }
  .footer-brand .brand-name { font-size: 18px; color: #c9d8de; }
</style>
</head>
<body>

<header class="abs site-header">
  <div class="abs brand">
    <span class="brand-dot"></span>
    <span class="brand-name">Velmarq Studio</span>
  </div>
  <span class="abs social" style="left:827px" aria-label="Social profile"></span>
  <span class="abs social" style="left:872px" aria-label="Social profile"></span>
  <span class="abs social" style="left:916px" aria-label="Social profile"></span>
</header>

<nav class="abs main-nav">
  <ul>
    <li class="active">Software Training and Implementation</li>
    <li>Project Management</li>
    <li>Business Process Analysis</li>
    <li>Blog</li>
    <li>About Us</li>
    <li>Contact</li>
  </ul>
</nav>

<section class="abs hero">
  <h1 class="abs hero-title"><span class="small">SPECIALIST BUSINESS</span><span class="big">CONSULTANTS</span></h1>
  <span class="abs qmark open">&ldquo;</span>
  <p class="abs hero-quote">Whatever the mind of man can con&shy;ceive and believe, it can achieve. Thoughts are things! And powerful things at that, when mixed with defi&shy;niteness of purpose, and burning desire, can be translated into riches</p>
  <span class="abs qmark close">&rdquo;</span>
  <div class="abs hero-visual" role="img" aria-label="Laptop displaying a photo of consultants shaking hands at a meeting table"></div>
  <div class="abs slider-dots"><span class="current"></span><span></span><span></span></div>
</section>

<section class="abs welcome">
  <h2 class="section-title">Welcome to Velmarq Studio</h2>
  <div class="welcome-body">
    <div class="welcome-photo" role="img" aria-label="Photo of a business team reviewing documents at a laptop"></div>
    <p>Cloud computing spending is due to account for a third of annual IT expenditure growth by the end of 2013. Every year the range of cloud software systems gets bigger, now including Brindlepath Accounting, Quillbase Suite for Business, Tallyframe Job Management Software, Corvane Desk 365, Plotwise Project Manager and many more. Signing up for cloud software is only the first part of the process, and then it has to be implemented into your business. That's where Velmarq Studio comes in.
    Formed in 2011, and with a history in cloud computing, implementation and support, we know there's much more to software implementation and effective business use than the purchase. We can assist by providing an external resource to assist with implementation, as well as getting the right processes post-implementation. Cloud software brings with it a huge array of benefits and efficiencies, but only if resourced and implemented correctly. Do you have somebody in your business that you can afford not to work in their role in order to implement? Having seen the negative impact this can have, we are there to help.</p>
  </div>
</section>

<section class="abs services">
  <h2 class="section-title">Our Services</h2>
  <ul>
    <li>Lorem Ipsum is simply dummy</li>
    <li>Text of the printing and typesetting</li>
    <li>Industry. Lorem Ipsum has been</li>
    <li>Industry's standard dummy text ever since</li>
    <li>when an unknown printer took a galley</li>
    <li>Type only five centuri</li>
    <li>Lorem Ipsum is simply dummy</li>
    <li>Text of the printing and typesetting</li>
    <li>Industry. Lorem Ipsum has been</li>
    <li>Type only five centuri</li>
  </ul>
</section>

<div class="abs footer-band"></div>

<article class="abs card blog">
  <h2 class="section-title">Blog Post</h2>
  <div class="card-arrows">
    <span><svg width="6" height="10" viewBox="0 0 6 10"><path d="M5 1 1 5l4 4" fill="none" stroke="#fff" stroke-width="1.2"/></svg></span>
    <span><svg width="6" height="10" viewBox="0 0 6 10"><path d="M1 1l4 4-4 4" fill="none" stroke="#fff" stroke-width="1.2"/></svg></span>
  </div>
  <span class="card-link">Corvane Mail to Quillbase Suite</span>
  <p>With Corvane making big strides recently to move their huge office suite into the cloud, with Corvane Desk 365,</p>
  <span class="card-link sub-link">So why Cloud Software...?</span>
  <p>Cloud software is a massive area of the market and has emerged as a viable choice for many areas of business in the last year</p>
</article>

<article class="abs card comments">
  <h2 class="section-title">Recent Comments</h2>
  <div class="card-arrows">
    <span><svg width="6" height="10" viewBox="0 0 6 10"><path d="M5 1 1 5l4 4" fill="none" stroke="#fff" stroke-width="1.2"/></svg></span>
    <span><svg width="6" height="10" viewBox="0 0 6 10"><path d="M1 1l4 4-4 4" fill="none" stroke="#fff" stroke-width="1.2"/></svg></span>
  </div>
  <span class="card-link">Corvane Mail to Quillbase Suite</span>
  <p>Lorem Ipsum is simply dummy text of the printing and typesetting industry. Lorem Ipsum has been the industry's standard dummy text ever since the 1500s, when an unknown printer took a galley of type only five centuries,</p>
  <p class="byline">By<br>Dr. Halloway</p>
</article>

<ul class="abs footer-nav">
  <li>Home</li>
  <li>Software Training and Implementation</li>
  <li>Blog</li>
  <li>About Us</li>
  <li>Project Management</li>
  <li>Business Process Analysis</li>
  <li>Contact us</li>
</ul>

<footer class="abs site-footer">
  <p class="abs copyright">Copyright &copy; 2013 Velmarq Studio All right reserved.&nbsp; Powered by</p>
  <div class="abs footer-brand">
    <span class="brand-dot"></span>
    <span class="brand-name">Velmarq Studio</span>
  </div>
</footer>

</body>
</html>
```